KAJU Freightways #ALLKAJU Business Cards & Letterhead

I am looking to business cards designed for our organization. We are currently undergoing a small re-branding that is taking place. Our organization is called KAJU Freightways and we are headquartered in Phoenix, AZ. We primarily provide transportation and logistics services to the Marlow Parcel Bureau who is our largest customer. I would like to see a design that incorporates name, title, contact info, website, and address (this will be different depending on the employee). I would also like to see some color on the business card using our logo colors or a variation. I would like our logo on the back of the business card with the website displayed. The final design should communicate that we are a next generation transportation operate that focuses on being driver-first, customer-centric, innovative, and sustainable.We would also like our #ALLKAJU catch phrase incorporated as well.

Target Market(s)

Transportation & Logistics

Industry/Entity Type

Trucking Company

Contact Information for Business Card

-First and Last Name
-Position Title
-Contact Phone
-Contact Email
-Physical Address

Font styles to use
Serif

Colors

Designer to choose colors to be used in the design.

Requirements
Must have
• -KAJU logo prominently displayed
• -#ALLKAJU catch phrase used
• -Some amount of color, design gradient, etc.
• -Logo on the back with website listed (https://www.kajufreightco.example)

```html
<!DOCTYPE html>
<html lang="en">
<head>
<meta charset="utf-8">
<title>KAJU Freightways Letterhead &amp; Business Cards</title>
<link rel="stylesheet" href="https://fonts.googleapis.com/css2?family=Lato:wght@400;700&family=Arimo:wght@400;700&family=Nothing+You+Could+Do&display=swap">
<style>
  :root{
    --navy:#143a45;
    --green:#7abd42;
    --paper:#f5f5f5;
    --ink:#1c1c1c;
    --stage:#e4e4e4;
    --ghost:rgba(255,255,255,0.08);
  }
  *{margin:0;padding:0;box-sizing:border-box}
  html,body{width:1200px;height:1200px;overflow:hidden;background:var(--stage)}
  .board{position:relative;width:1200px;height:1200px}
  .sheet{position:absolute;transform-origin:top left;transform:scale(0.621);background:var(--paper);overflow:hidden}
  .sheet > svg.art{position:absolute;left:0;top:0}
  .letterhead{left:89px;top:145px;width:1121px;height:1450px}
  .card{width:462px;height:264px}
  .card-back{left:835px;top:271px;background:var(--navy)}
  .card-front{left:835px;top:460px}
  .abs{position:absolute}
  .brand-mark{position:absolute;border-radius:50%;background:var(--paper);border:5px solid var(--green);display:flex;align-items:center;justify-content:center;font-family:'Lato',sans-serif;font-weight:700;color:var(--navy)}
  .divider{position:absolute;width:2px}
  .tagline{position:absolute;font-family:'Lato',sans-serif;color:var(--green);line-height:1.25}
  .company-block{position:absolute;right:87px;top:78px;text-align:right;font-family:'Lato',sans-serif;color:var(--navy);font-size:16.5px;line-height:20px}
  .company-block b{font-weight:700}
  .contact-list{margin-top:10px}
  .contact-list div{display:flex;justify-content:flex-end;align-items:center;gap:6px}
  .icon{width:13px;height:13px;flex:none}
  .letter{position:absolute;left:87px;top:362px;width:960px;font-family:'Arimo',sans-serif;font-size:16.5px;line-height:22px;color:var(--ink)}
  .letter p{margin-bottom:22px;text-align:justify}
  .letter .date{margin-bottom:22px}
  .letter .recipient{margin-bottom:44px;text-align:left}
  .letter .salutation{font-weight:700;margin-bottom:44px}
  .letter .closing{margin-top:64px;margin-bottom:14px}
  .signature{font-family:'Nothing You Could Do',cursive;font-size:30px;line-height:44px;margin-bottom:16px}
  .hashtag{position:absolute;font-family:'Lato',sans-serif;color:#fff;font-weight:400}
  .hashtag span{color:var(--green)}
  .card-web{position:absolute;left:0;right:0;top:221px;text-align:center;font-family:'Lato',sans-serif;font-size:11.5px;letter-spacing:2px;color:#fff}
  .card-web span,.green{color:var(--green)}
  .person{position:absolute;right:33px;top:54px;text-align:right;font-family:'Lato',sans-serif}
  .person-name{color:var(--green);font-size:16px;font-weight:700;letter-spacing:0.2px}
  .person-title{color:var(--navy);font-size:12px;margin-top:2px}
  .card-details{position:absolute;left:32px;top:128px;font-family:'Lato',sans-serif;color:var(--navy);font-size:11.5px;line-height:15px}
  .card-details b{font-size:12.5px}
  .card-details .contact-list{margin-top:6px}
  .card-details .contact-list div{justify-content:flex-start;gap:4px}
  .card-details .icon{width:10px;height:10px}
</style>
</head>
<body>
<div class="board">

  <!-- Letterhead -->
  <section class="sheet letterhead" aria-label="KAJU Freightways letterhead">
    <svg class="art" width="1121" height="1450" viewBox="0 0 1121 1450" aria-hidden="true">
      <path d="M0 0 H400 Q170 80 0 248 Z" fill="var(--green)"/>
      <path d="M0 0 H328 Q130 92 0 232 Z" fill="var(--navy)"/>
      <path d="M0 1352 Q560 1530 1121 1177 V1450 H0 Z" fill="var(--green)"/>
      <path d="M0 1398 Q620 1470 1121 1186 V1450 H0 Z" fill="var(--navy)"/>
      <circle cx="973" cy="1386" r="128" fill="none" stroke="var(--ghost)" stroke-width="6"/>
    </svg>

    <div class="brand-mark" style="left:84px;top:75px;width:140px;height:140px;font-size:36px">KAJU</div>
    <div class="divider" style="left:248px;top:75px;height:142px;background:var(--navy)"></div>
    <div class="tagline" style="left:273px;top:115px;font-size:24px">Transportation<br>and Energy Services</div>

    <div class="company-block">
      <b>KAJU Freightways &amp; Energy Services, Inc.</b><br>
      4410 North Cactus Ridge Road<br>
      Mesa, AZ 85201
      <div class="contact-list">
        <div>555-014-2290
          <svg class="icon" viewBox="0 0 16 16"><path d="M3 1l3 3-1.5 2a9 9 0 0 0 5 5L11.5 9.5l3 3L13 15C7 15 1 9 1 3z" fill="var(--green)"/></svg></div>
        <div>info@kajufreightco.example
          <svg class="icon" viewBox="0 0 16 16"><rect x="1" y="3" width="14" height="10" fill="none" stroke="var(--green)" stroke-width="1.6"/><path d="M1 3l7 6 7-6" fill="none" stroke="var(--green)" stroke-width="1.6"/></svg></div>
        <div>www.kajufreightco.example
          <svg class="icon" viewBox="0 0 16 16"><circle cx="8" cy="8" r="6.5" fill="none" stroke="var(--green)" stroke-width="1.4"/><path d="M1.5 8h13M8 1.5c-3 3-3 10 0 13M8 1.5c3 3 3 10 0 13" fill="none" stroke="var(--green)" stroke-width="1.2"/></svg></div>
      </div>
    </div>

    <article class="letter">
      <p class="date">November 15, 2019</p>
      <p class="recipient">Mr. Alan Pryce<br>President<br>Birchline Corporation<br>111 Street Name, Suite#<br>City, State, 12345</p>
      <p class="salutation">Dear Mr. Alan,</p>
      <p>Lorem ipsum dolor sit amet, consectetur adipiscing elit. Integer diam quam, egestas eu ultrices eu, suscipit ac sapien. Phasellus eu dui nisi. Nam et euismod diam, nec lobortis tortor. Donec et diam nulla. Aenean varius tincidunt convallis. Aliquam a tortor at lacus dictum aliquet. Nunc laoreet metus sapien, in scelerisque augue consectetur in.</p>
      <p>Fusce nec justo laoreet, egestas justo sed, aliquet sem. Pellentesque pharetra massa non orci bibendum semper. Pellentesque cursus eu lectus a consectetur. Nunc volutpat suscipit posuere. Vestibulum facilisis vel quam malesuada mattis. Nulla in mattis tellus. Maecenas tristique mauris vitae pharetra tincidunt. In ut ornare risus. Integer molestie vestibulum nisi, semper dapibus mi condimentum eu.</p>
      <p>Nullam sagittis elit libero, id fringilla est tincidunt eget. Donec in ipsum ultricies, consectetur quam vel, facilisis elit. Phasellus tincidunt congue risus vel luctus. Suspendisse ut mollis neque. Donec ornare orci in turpis vestibulum, in ultrices metus scelerisque. Pellentesque mattis mattis nunc, nec tincidunt lacus egestas id. Fusce facilisis sagittis neque sit amet vulputate. Aliquam ut eros lobortis tortor facilisis vehicula. Sed sed luctus leo, at laoreet sapien. Donec placerat adipiscing ligula non euismod. In lobortis pretium nisl id luctus.</p>
      <p>Integer gravida tincidunt nibh, scelerisque tincidunt turpis. Suspendisse potenti. Nunc hendrerit euismod lectus id elementum. Fusce vitae gravida velit, quis eleifend lectus. In imperdiet mauris eu dui viverra sagittis. Donec tempor dui diam, condimentum gravida lacus pretium a. Nullam fringilla augue quis arcu placerat scelerisque.</p>
      <p class="closing">Sincerely Yours,</p>
      <div class="signature">Rena Halvorsen</div>
      <p style="text-align:left">Rena Halvorsen<br>President</p>
    </article>

    <div class="hashtag" style="left:918px;top:1372px;font-size:20px"><span>#</span>ALLKAJU</div>
  </section>

  <!-- Business card back -->
  <section class="sheet card card-back" aria-label="Business card back">
    <div class="brand-mark" style="left:97px;top:88px;width:90px;height:90px;font-size:23px;border-width:3.5px;background:var(--navy);color:#fff">KAJU</div>
    <div class="divider" style="left:204px;top:85px;height:96px;background:#fff"></div>
    <div class="tagline" style="left:221px;top:112px;font-size:15.5px">Transportation<br>and Energy Services</div>
    <div class="card-web">www.<span>kajufreightco</span>.example</div>
  </section>

  <!-- Business card front -->
  <section class="sheet card card-front" aria-label="Business card front">
    <svg class="art" width="462" height="264" viewBox="0 0 462 264" aria-hidden="true">
      <path d="M0 0 H188 Q70 48 0 118 Z" fill="var(--green)"/>
      <path d="M0 0 H152 Q58 52 0 110 Z" fill="var(--navy)"/>
      <path d="M0 230 Q250 272 462 152 V264 H0 Z" fill="var(--green)"/>
      <path d="M0 246 Q270 262 462 162 V264 H0 Z" fill="var(--navy)"/>
      <circle cx="392" cy="234" r="58" fill="none" stroke="var(--ghost)" stroke-width="3"/>
    </svg>
    <div class="brand-mark" style="left:32px;top:26px;width:90px;height:90px;font-size:23px;border-width:3.5px">KAJU</div>
    <div class="person">
      <div class="person-name">RENA HALVORSEN</div>
      <div class="person-title">President</div>
    </div>
    <div class="card-details">
      <b>KAJU Freightways &amp; Energy Services, Inc.</b><br>
      4410 North Cactus Ridge Road<br>
      Mesa, AZ 85201
      <div class="contact-list">
        <div><svg class="icon" viewBox="0 0 16 16"><path d="M3 1l3 3-1.5 2a9 9 0 0 0 5 5L11.5 9.5l3 3L13 15C7 15 1 9 1 3z" fill="var(--green)"/></svg>555-014-2290</div>
        <div><svg class="icon" viewBox="0 0 16 16"><rect x="1" y="3" width="14" height="10" fill="none" stroke="var(--green)" stroke-width="1.8"/><path d="M1 3l7 6 7-6" fill="none" stroke="var(--green)" stroke-width="1.8"/></svg>rena@kajufreightco.example</div>
        <div><svg class="icon" viewBox="0 0 16 16"><circle cx="8" cy="8" r="6.5" fill="none" stroke="var(--green)" stroke-width="1.6"/><path d="M1.5 8h13M8 1.5c-3 3-3 10 0 13M8 1.5c3 3 3 10 0 13" fill="none" stroke="var(--green)" stroke-width="1.3"/></svg>www.<span class="green">kajufreightco</span>.example</div>
      </div>
    </div>
    <div class="hashtag" style="left:362px;top:224px;font-size:13px"><span>#</span>ALLKAJU</div>
  </section>

</div>
</body>
</html>
```